Two Separate Canvas Posters 54"width x 36" Height

I need two (2) posters designed for a new restaurant concept called: Lumara Fresh Pita Grill.
Both posters will be printed on Canvas and placed into our new restaurants dining area.
I want this to look hip and cool.
I want so see red colors and earth tones. Please see attached for some ideas that I have.
The final design should communicate that you really gotta have this product and that this is a fun and casual place for a quick bite on the go.
Poster 1 message: gotta Eatta pita!
Size: 54"width x 36" high
Idea: Please see attached for design ideas and colors that I would like to see. If you can come up with any better idea, I would love to see this.
Poster 2 message: Power to the Pita
Size: 54"width x 36" height
Idea: Please see attached for design idea and colors that I want to see.
Industry/Entity Type
Restaurant
Look and feel
Each slider illustrates characteristics of the customer's brand and the style your logo design should communicate.

```html
<!DOCTYPE html>
<html lang="en">
<head>
<meta charset="utf-8">
<title>gotta Eatta pita</title>
<link href="https://fonts.googleapis.com/css2?family=Jost:wght@500;600&display=swap" rel="stylesheet">
<style>
  :root {
    --bg-deep: #2b0202;
    --bg-warm: #470909;
    --ghost: #5a1c0c;
    --ghost-soft: #4d1509;
    --gotta: #f6a460;
    --eatta: #d4640f;
    --pita: #f7923a;
    --petal: #d8000c;
    --petal-light: #f0101a;
    --petal-dark: #7a0006;
  }
  html, body {
    margin: 0;
    padding: 0;
    overflow: hidden;
    background: var(--bg-deep);
  }
  .poster {
    display: block;
    width: 1200px;
    height: 800px;
  }
  .headline {
    font-family: "Jost", "Century Gothic", sans-serif;
    font-weight: 600;
  }
  .word { filter: drop-shadow(5px 7px 5px rgba(0,0,0,.65)); }
  .word--gotta { fill: var(--gotta); }
  .word--eatta { fill: var(--eatta); }
  .word--pita  { fill: var(--pita); }
  .echo { fill: var(--ghost); opacity: .7; }
  .echo--soft { fill: var(--ghost-soft); }
</style>
</head>
<body>
<svg class="poster" viewBox="0 0 1200 800" xmlns="http://www.w3.org/2000/svg">
  <defs>
    <radialGradient id="backdrop" cx="55%" cy="45%" r="75%">
      <stop offset="0" stop-color="var(--bg-warm)"/>
      <stop offset="1" stop-color="var(--bg-deep)"/>
    </radialGradient>
    <radialGradient id="petal-tone" cx="40%" cy="60%" r="70%">
      <stop offset="0" stop-color="var(--petal-light)"/>
      <stop offset=".75" stop-color="var(--petal)"/>
      <stop offset="1" stop-color="var(--petal-dark)"/>
    </radialGradient>
  </defs>

  <rect class="backdrop" width="1200" height="800" fill="url(#backdrop)"/>

  <g class="headline echoes">
    <text class="echo echo--soft" transform="translate(170,330) rotate(-40)" font-size="240" textLength="520" lengthAdjust="spacing">gotta</text>
    <text class="echo" transform="translate(560,470) rotate(-32)" font-size="300" textLength="640" lengthAdjust="spacing">Eatta</text>
    <text class="echo echo--soft" transform="translate(640,790) rotate(-4)" font-size="240" textLength="440" lengthAdjust="spacing">pita</text>
  </g>

  <g class="petal-shadow" role="img" aria-label="Dark red petal shadow">
    <ellipse cx="320" cy="460" rx="160" ry="85" fill="var(--petal-dark)" opacity=".8"/>
  </g>

  <g class="headline">
    <text class="word word--gotta" transform="translate(195,480) rotate(-40)" font-size="225" textLength="560" lengthAdjust="spacing">gotta</text>
    <text class="word word--eatta" transform="translate(430,570) rotate(-30)" font-size="320" textLength="740" lengthAdjust="spacing">Eatta</text>
    <text class="word word--pita" transform="translate(595,575) rotate(-4)" font-size="240" textLength="460" lengthAdjust="spacing">pita</text>
  </g>

  <path class="petal" role="img" aria-label="Red rose petal illustration"
        fill="url(#petal-tone)"
        d="M0,540 C30,500 90,440 150,410 C210,395 260,420 300,445 C360,462 430,480 480,500 C530,520 560,550 575,590 C600,660 630,730 660,800 L0,800 Z"/>
</svg>
</body>
</html>
```